Luxury WordPress Website for CORALBASINS

I need a professional WordPress website for Coral Basins. The site should be modern, visually appealing, and user-friendly, reflecting the brand’s luxury and premium identity. It must include a homepage, product/service pages, contact form, and be responsive on both desktop and mobile devices. The design should allow for easy updates and integration of future content, while maintaining a polished and professional look.

Target Market(s)

swimmingpool & spa

Industry/Entity Type

Swimmingpool

Coding

Coded - Design and coding required

Font styles to use
Other font styles liked:
• HaboroSoft

Requirements
Must have
• Exclusive appearance
Nice to have
• • A logo that subtly incorporates water or pool elements. • A color palette that reflects luxury, elegance, and relaxation. • Clean and modern typography that is easy to read across all media. • Iconography or design elements that convey premium quality. • A versatile design that can be adapted for social media, merchandise, and promotional materials. • Optional: A tagline that emphasizes luxury and high-end pool experiences.

```html
<!DOCTYPE html>
<html lang="en">
<head>
<meta charset="utf-8">
<title>Coral Basins — Luxury Pools</title>
<link href="https://fonts.googleapis.com/css2?family=Poppins:ital,wght@0,400;0,500;0,600;1,400&display=swap" rel="stylesheet">
<style>
:root{
  --blue:#1d8fd8;
  --blue-deep:#0f6aa8;
  --yellow:#f7b900;
  --ink:#1e1e1e;
  --text:#3a3a3a;
  --muted:#f3f3f3;
  --dark:#2c2c2c;
  --white:#fff;
}
*{margin:0;padding:0;box-sizing:border-box}
html,body{width:1200px;height:3860px;overflow:hidden}
body{font-family:"Poppins",sans-serif;color:var(--ink);background:var(--white);position:relative}
.abs{position:absolute}
.btn{position:absolute;display:flex;align-items:center;justify-content:center;font-weight:500;color:var(--white);font-size:16px}
.btn--yellow{background:var(--yellow)}
.btn--blue{background:var(--blue)}

/* header */
.brand{left:75px;top:26px;display:flex;align-items:center;gap:10px;font-weight:600;font-size:22px;color:var(--blue)}
.brand__dot{width:16px;height:16px;border-radius:50%;background:var(--blue)}
.nav{left:372px;top:42px;display:flex;gap:40px;font-size:15px;font-weight:500;color:#222}
.nav a{color:inherit;text-decoration:none}
.nav .is-active{color:var(--blue)}
.phone{left:930px;top:32px;display:flex;align-items:center;gap:12px;font-size:20px;font-weight:500}
.phone__icon{width:45px;height:45px;border-radius:50%;background:var(--blue);display:flex;align-items:center;justify-content:center}

/* hero */
.hero-bg{left:0;top:0;width:1200px;height:640px;background:linear-gradient(90deg,#e9f4fb 0%,#dcecf6 40%,#c9dfe9 60%,#b99a76 80%,#8aa36e 100%)}
.hero-pool{left:260px;top:330px;width:500px;height:240px;background:linear-gradient(180deg,#7fd3f0,#2fa6de);opacity:.7;border-radius:6px}
.hero-title{left:72px;top:188px;font-size:47px;font-weight:500;line-height:1.05;color:#1a1a1a}
.hero-sub{left:73px;top:300px;font-size:22px;font-weight:500;line-height:1.35;color:#1a1a1a}
.cats{left:0;top:0}
.cat{position:absolute;width:212px;height:212px;border-radius:50%;border:6px solid #fff;box-shadow:0 2px 8px rgba(0,0,0,.15)}
.cat--active{border-color:var(--yellow)}
.cat-label{position:absolute;width:174px;height:40px;background:var(--yellow);color:#fff;font-weight:500;font-size:18px;display:flex;align-items:center;justify-content:center}

/* welcome */
.welcome-img{left:0;top:832px;width:586px;height:325px;background:linear-gradient(160deg,#5e8a4a,#3aa7e0 55%,#7dc4e8);clip-path:polygon(0 0,100% 0,82% 100%,0 100%)}
.h2{font-size:35px;font-weight:500;line-height:1.15;color:#222}
.para{font-size:15px;line-height:26px;color:var(--text)}

/* services */
.services-bg{left:0;top:1220px;width:1200px;height:510px}
.svc-title{left:73px;top:1302px;color:#fff}
.svc{position:absolute;width:250px;text-align:center;color:#fff}
.svc__icon{width:124px;height:124px;border-radius:50%;background:var(--yellow);border:5px solid #fff;margin:0 auto;display:flex;align-items:center;justify-content:center}
.svc__name{margin-top:22px;font-size:17px;font-weight:500;line-height:24px}
.svc__desc{margin-top:6px;font-size:15px;line-height:22px;color:#e9f5ff}

/* projects */
.proj{position:absolute;width:328px}
.proj__img{height:198px}
.proj__name{margin-top:20px;font-size:21px;font-weight:500}
.proj__desc{margin-top:10px;font-size:15px;line-height:25px;color:var(--text)}
.proj-card{left:419px;top:1859px;width:361px;height:431px;background:var(--muted)}

/* testimonials */
.testi-bg{left:0;top:2410px;width:1200px;height:590px}
.quote{position:absolute;width:511px;height:170px;background:#fff;box-shadow:0 2px 10px rgba(0,0,0,.08)}
.quote__avatar{position:absolute;left:18px;top:22px;width:130px;height:130px;border-radius:50%;background:linear-gradient(135deg,#f7b900,#2fa6de)}
.quote__text{position:absolute;left:170px;top:26px;width:320px;font-size:15px;line-height:22px;font-style:italic;color:#222}
.quote__name{position:absolute;left:170px;top:122px;font-size:15px;font-weight:600;color:var(--blue)}

/* contact */
.field{position:absolute;border:1px solid #cfcfcf;font-size:13px;color:#333;padding:14px 14px}
.contact-img{left:617px;top:3078px;width:583px;height:324px;background:linear-gradient(120deg,#e9e4dc,#c9b59b 50%,#8a7462);clip-path:polygon(0 0,100% 0,100% 100%,10% 100%)}

/* footer */
.footer-bg{left:0;top:3440px;width:1200px;height:420px}
.f-brand{left:75px;top:3620px;display:flex;align-items:center;gap:12px;font-size:30px;font-weight:500;color:#9a9a9a}
.f-brand__dot{width:22px;height:22px;border-radius:50%;background:#9a9a9a}
.f-col{position:absolute;color:#fff}
.f-col h4{font-size:15px;font-weight:600;margin-bottom:14px}
.f-col p{font-size:14px;line-height:36px;color:#e6e6e6}
.socials{display:flex;gap:16px;margin-top:10px}
.socials span{width:20px;height:20px;border-radius:50%;background:#fff}
.copy{left:0;top:3822px;width:1200px;text-align:center;font-size:12px;color:#e6e6e6}
</style>
</head>
<body>

<!-- HERO -->
<div class="abs hero-bg" role="img" aria-label="Modern house with a pool and a smiling consultant holding a folder"></div>
<div class="abs hero-pool" role="img" aria-label="Pool water"></div>
<svg class="abs" style="left:0;top:520px" width="1200" height="200" viewBox="0 0 1200 200">
  <path d="M0 95 C200 70 330 110 560 110 C760 110 980 40 1200 85 L1200 200 L0 200Z" fill="var(--blue)"/>
  <path d="M0 104 C200 82 330 124 560 122 C760 120 980 56 1200 100 L1200 200 L0 200Z" fill="#fff"/>
</svg>

<div class="abs brand"><span class="brand__dot"></span>Coral Basins</div>
<nav class="abs nav">
  <a class="is-active">Home</a><a>About Us</a><a>Services</a><a>Project Gallery</a><a>Contact Us</a>
</nav>
<div class="abs phone">
  <span class="phone__icon"><svg width="20" height="20" viewBox="0 0 24 24"><path fill="#fff" d="M6.6 10.8a15 15 0 0 0 6.6 6.6l2.2-2.2c.3-.3.7-.4 1-.2 1.1.4 2.3.6 3.6.6.6 0 1 .4 1 1V20c0 .6-.4 1-1 1A17 17 0 0 1 3 4c0-.6.4-1 1-1h3.5c.6 0 1 .4 1 1 0 1.3.2 2.5.6 3.6.1.3 0 .7-.2 1z"/></svg></span>
  +1 555-010-2040
</div>

<h1 class="abs hero-title">Experience the Art of<br>Luxury Living</h1>
<p class="abs hero-sub">Exclusive pools crafted for design, durability,<br>and perfection.</p>
<div class="btn btn--yellow" style="left:75px;top:382px;width:241px;height:50px">Explore Our Collections</div>

<div class="cat" style="left:91px;top:519px;background:linear-gradient(180deg,#d9cfc0,#2f9ad6)" role="img" aria-label="Indoor infinity pool"></div>
<div class="cat cat--active" style="left:360px;top:519px;background:linear-gradient(180deg,#9cb7cf,#4cb8e4)" role="img" aria-label="Designer pool at a large home"></div>
<div class="cat" style="left:630px;top:519px;background:linear-gradient(180deg,#e2d6a8,#1f8fd4)" role="img" aria-label="Family pool in a backyard"></div>
<div class="cat" style="left:900px;top:519px;background:linear-gradient(180deg,#dcdcdc,#9a5a32)" role="img" aria-label="Custom pool under construction"></div>
<div class="cat-label" style="left:110px;top:707px">Infinity Pools</div>
<div class="cat-label" style="left:379px;top:707px">Designer Pools</div>
<div class="cat-label" style="left:649px;top:707px">Family Pools</div>
<div class="cat-label" style="left:919px;top:707px">Custom Builds</div>

<!-- WELCOME -->
<div class="abs welcome-img" role="img" aria-label="Backyard pool with umbrellas and lounge chairs"></div>
<h2 class="abs h2" style="left:615px;top:824px">Welcome to<br>Coral Basins</h2>
<p class="abs para" style="left:615px;top:918px;width:515px">Nemo enim ipsam voluptatem quia voluptas sit aspernatur aut odit aut fugit, sed quia consequuntur magni dolores eos qui ratione voluptatem sequi nesciunt. Neque porro quisquam est, qui dolorem ipsum quia dolor sit amet, consectetur, adipisci velit, sed quia non numquam eius modi tempora incidunt ut labore et dolore magnam aliquam quaerat voluptatem.</p>
<div class="btn btn--yellow" style="left:615px;top:1103px;width:150px;height:54px">Read More</div>

<!-- SERVICES -->
<svg class="abs services-bg" viewBox="0 0 1200 510" role="img" aria-label="Blue pool water background">
  <defs><linearGradient id="svcg" x1="0" y1="0" x2="1" y2="1"><stop offset="0" stop-color="#1a86c7"/><stop offset=".5" stop-color="#0f6aa8"/><stop offset="1" stop-color="#1a7fbd"/></linearGradient></defs>
  <path d="M0 30 C300 -10 700 -10 1200 40 L1200 460 C900 500 600 520 300 480 C180 465 80 460 0 470Z" fill="url(#svcg)"/>
</svg>
<h2 class="abs h2 svc-title">Our Services</h2>
<svg class="abs" style="left:1042px;top:1310px" width="90" height="30" viewBox="0 0 90 30">
  <path d="M30 15H6M15 5 5 15l10 10" stroke="#fff" stroke-width="5" fill="none"/>
  <path d="M56 15h24M71 5l10 10-10 10" stroke="var(--yellow)" stroke-width="5" fill="none"/>
</svg>
<div class="svc" style="left:71px;top:1370px">
  <div class="svc__icon"><svg width="50" height="50" viewBox="0 0 50 50" fill="none" stroke="#222" stroke-width="2.5"><rect x="10" y="8" width="30" height="34" rx="3"/><path d="M15 20q5-4 10 0t10 0M15 28q5-4 10 0t10 0"/></svg></div>
  <div class="svc__name">Custom Pool Design<br>&amp; Construction</div>
  <div class="svc__desc">Nemo enim ipsam voluptatem quia voluptas sit aspernatur aut odit aut fugit.</div>
</div>
<div class="svc" style="left:341px;top:1370px">
  <div class="svc__icon"><svg width="50" height="50" viewBox="0 0 50 50" fill="none" stroke="#222" stroke-width="2.5"><rect x="9" y="9" width="32" height="32" rx="3"/><path d="M18 24h14v6l-7 5-7-5z"/></svg></div>
  <div class="svc__name">Renovation<br>&amp; Remodeling</div>
  <div class="svc__desc">Nemo enim ipsam voluptatem quia voluptas sit aspernatur aut odit aut fugit.</div>
</div>
<div class="svc" style="left:611px;top:1370px">
  <div class="svc__icon"><svg width="50" height="50" viewBox="0 0 50 50" fill="none" stroke="#222" stroke-width="2.5"><rect x="9" y="9" width="32" height="32" rx="3"/><path d="M17 34l12-12m0 0a5 5 0 1 0 4-4"/></svg></div>
  <div class="svc__name">Maintenance &amp;<br>Water Care</div>
  <div class="svc__desc">Nemo enim ipsam voluptatem quia voluptas sit aspernatur aut odit aut fugit.</div>
</div>
<div class="svc" style="left:881px;top:1370px">
  <div class="svc__icon"><svg width="50" height="50" viewBox="0 0 50 50" fill="none" stroke="#222" stroke-width="2.5"><rect x="8" y="18" width="34" height="22" rx="3"/><path d="M18 18v-6m8 6V9m8 9v-6"/></svg></div>
  <div class="svc__name">Outdoor Living &amp;<br>Landscaping</div>
  <div class="svc__desc">Nemo enim ipsam voluptatem quia voluptas sit aspernatur aut odit aut fugit.</div>
</div>

<!-- PROJECTS -->
<h2 class="abs h2" style="left:0;width:1200px;text-align:center;top:1786px">Featured Projects</h2>
<div class="abs proj-card"></div>
<div class="proj" style="left:75px;top:1859px">
  <div class="proj__img" role="img" aria-label="Pool wall panels on a dirt site" style="background:linear-gradient(160deg,#d8d2c8,#a8552a)"></div>
  <div class="proj__name">Project Heading</div>
  <div class="proj__desc">Nemo enim ipsam voluptatem quia voluptas sit aspernatur..</div>
</div>
<div class="proj" style="left:436px;top:1875px">
  <div class="proj__img" role="img" aria-label="Lit freeform pool at dusk, seen from above" style="background:linear-gradient(160deg,#8a8fa8,#1d5fc9 55%,#6b6f86)"></div>
  <div class="proj__name">Project Heading</div>
  <div class="proj__desc">Nemo enim ipsam voluptatem quia voluptas sit aspernatur &nbsp;aut odit aut fugit, sed quiaaute irure dolor.</div>
</div>
<div class="btn btn--blue" style="left:437px;top:2219px;width:136px;height:43px;font-size:15px">Read More</div>
<div class="proj" style="left:798px;top:1859px">
  <div class="proj__img" role="img" aria-label="Pool steps installed in an excavated site" style="background:linear-gradient(160deg,#e6e6e6,#b0b0b0 45%,#9a4e28)"></div>
  <div class="proj__name">Project Heading</div>
  <div class="proj__desc">Nemo enim ipsam voluptatem quia voluptas sit aspernatur..</div>
</div>
<svg class="abs" style="left:558px;top:2330px" width="84" height="30" viewBox="0 0 84 30">
  <path d="M30 15H6M15 5 5 15l10 10" stroke="#555" stroke-width="5" fill="none"/>
  <path d="M52 15h24M67 5l10 10-10 10" stroke="var(--yellow)" stroke-width="5" fill="none"/>
</svg>

<!-- TESTIMONIALS -->
<svg class="abs testi-bg" viewBox="0 0 1200 590" role="img" aria-label="Blurred poolside greenery and water">
  <defs><linearGradient id="tg" x1="0" y1="0" x2="0" y2="1"><stop offset="0" stop-color="#dbe8d8"/><stop offset=".45" stop-color="#cfe3ea"/><stop offset="1" stop-color="#4fb2e6"/></linearGradient></defs>
  <path d="M0 30 C250 -10 500 20 700 30 C900 40 1050 20 1200 10 L1200 540 C950 600 700 560 500 540 C300 520 120 520 0 560Z" fill="url(#tg)"/>
  <path d="M0 30 C250 -10 500 20 700 30 C900 40 1050 20 1200 10" stroke="var(--blue)" stroke-width="8" fill="none"/>
  <path d="M0 560 C120 520 300 520 500 540 C700 560 950 600 1200 540" stroke="var(--blue)" stroke-width="10" fill="none"/>
</svg>
<h2 class="abs h2" style="left:0;width:1200px;text-align:center;top:2558px">Client Testimonials</h2>
<div class="quote" style="left:75px;top:2630px">
  <div class="quote__avatar" role="img" aria-label="Client portrait"></div>
  <p class="quote__text">“ | Duis aute irure dolor in reprehenderit in voluptate velit esse cillum dolore eu fugiat nulla pariatur. Excepteur sint occaecat cupidatat non proident, sunt..</p>
  <div class="quote__name">Name Heading</div>
</div>
<div class="quote" style="left:616px;top:2630px">
  <div class="quote__avatar" role="img" aria-label="Client portrait"></div>
  <p class="quote__text">“ | Duis aute irure dolor in reprehenderit in voluptate velit esse cillum dolore eu fugiat nulla pariatur. Excepteur sint occaecat cupidatat non proident, sunt..</p>
  <div class="quote__name">Name Heading</div>
</div>
<svg class="abs" style="left:558px;top:2840px" width="84" height="30" viewBox="0 0 84 30">
  <path d="M30 15H6M15 5 5 15l10 10" stroke="#555" stroke-width="5" fill="none"/>
  <path d="M52 15h24M67 5l10 10-10 10" stroke="var(--yellow)" stroke-width="5" fill="none"/>
</svg>

<!-- CONTACT -->
<h2 class="abs h2" style="left:73px;top:3052px">Quick Contact</h2>
<div class="field" style="left:75px;top:3118px;width:248px;height:45px">Name</div>
<div class="field" style="left:338px;top:3118px;width:248px;height:45px">Email Address</div>
<div class="field" style="left:75px;top:3176px;width:248px;height:45px">Phone No</div>
<div class="field" style="left:338px;top:3176px;width:248px;height:45px">Subject</div>
<div class="field" style="left:75px;top:3235px;width:511px;height:87px;padding-top:10px">Message</div>
<div class="btn btn--yellow" style="left:75px;top:3334px;width:145px;height:53px">Submit</div>
<div class="abs contact-img" role="img" aria-label="Consultants shaking hands with clients in an office"></div>

<!-- FOOTER -->
<svg class="abs footer-bg" viewBox="0 0 1200 420">
  <path d="M0 40 C300 10 900 10 1200 40 L1200 420 L0 420Z" fill="var(--dark)"/>
  <rect x="0" y="352" width="1200" height="2" fill="#3d3d3d"/>
</svg>
<div class="abs f-brand"><span class="f-brand__dot"></span>Coral Basins</div>
<div class="f-col" style="left:375px;top:3536px">
  <h4>QUICK LINKS</h4>
  <p>Home<br>About Us<br>Services<br>Project Gallery<br>Contatc Us</p>
</div>
<div class="f-col" style="left:621px;top:3536px">
  <h4>OUR POOLS</h4>
  <p>Infinity Pools<br>Designer Pools<br>Family Pools<br>Custom Builds</p>
</div>
<div class="f-col" style="left:882px;top:3536px">
  <h4>CONTACT INFO</h4>
  <p style="line-height:21px">48 Harbor Lane, Suite 12,<br>Miami 33101, United States</p>
  <p>+1 555-010-2040<br>hello@coralbasins.example</p>
  <div class="socials"><span></span><span></span><span></span><span></span><span></span></div>
</div>
<div class="abs copy">Copyright © 2025 Coral Basins All rights reserved.</div>

</body>
</html>
```